Kesso Tea Premium Matcha brand Label

This is a label design project for a luxury tea brand. Feel free to be creative within the guidelines.
Attached to this project is a document called “Private Label Design Requirements” with the design guidelines and template. There is another document called "Kesso Tea Packaging Instructions" this has more details necessary to stick to the guidelines in the first document.

I have also attached the certifications to be included as well as different variations of the logo for you to use.

If you have any questions, I am here.
Updates

Need extra days to review

Target Market(s)

Young, active, fun, enjoy the finer things

```html
<!DOCTYPE html>
<html lang="en">
<head>
<meta charset="utf-8">
<title>Kesso Tea Premium Organic Ceremonial Matcha Labels</title>
<link href="https://fonts.googleapis.com/css2?family=Montserrat:wght@500;600;700&display=swap" rel="stylesheet">
<style>
  :root {
    --backdrop: #1d1d1d;
    --label-white: #ffffff;
    --label-shade: #ececec;
    --ink: #1a1a1a;
    --matcha: #4fae3d;
    --badge-blue: #2f7cc0;
    --badge-green: #3d8c3a;
  }
  * { margin: 0; padding: 0; box-sizing: border-box; }
  html, body {
    width: 1200px; height: 631px; overflow: hidden;
    background: var(--backdrop);
    font-family: "Montserrat", sans-serif;
    color: var(--ink);
  }
  .canvas { position: relative; width: 1200px; height: 631px; }

  .lid-label {
    position: absolute; left: 40px; top: 150px;
    width: 330px; height: 330px; border-radius: 50%;
    background: radial-gradient(circle at 30% 30%, var(--label-white) 40%, var(--label-shade) 100%);
    box-shadow: 0 8px 18px rgba(0,0,0,.45);
    overflow: hidden;
  }
  .wrap-label {
    position: absolute; left: 395px; top: 240px;
    width: 770px; height: 150px;
    background: linear-gradient(160deg, var(--label-shade) 0%, var(--label-white) 35%, var(--label-white) 70%, var(--label-shade) 100%);
    box-shadow: 0 8px 18px rgba(0,0,0,.45);
  }

  .brand-mark {
    position: absolute; left: 0; right: 0;
    display: flex; flex-direction: column; align-items: center;
  }
  .brand-dot { border-radius: 50%; background: var(--matcha); }
  .brand-name { font-weight: 700; color: var(--ink); white-space: nowrap; }

  .product-title {
    position: absolute; left: 0; right: 0; text-align: center;
    font-weight: 700; text-transform: uppercase; letter-spacing: .02em;
  }
  .product-title .accent { color: var(--matcha); }
  .net-weight { position: absolute; left: 0; right: 0; text-align: center; font-weight: 600; }
  .title-frame { position: absolute; overflow: visible; }
  .title-frame polyline { fill: none; stroke: var(--ink); }

  /* lid */
  .lid-label .brand-mark { top: 58px; }
  .lid-label .brand-dot { width: 46px; height: 46px; }
  .lid-label .brand-name { font-size: 17px; margin-top: 8px; }
  .lid-label .product-title { top: 152px; font-size: 24px; line-height: 26px; }
  .lid-label .net-weight { top: 268px; font-size: 21px; }

  /* wrap */
  .wrap-label .brand-mark { top: 20px; }
  .wrap-label .brand-dot { width: 30px; height: 30px; }
  .wrap-label .brand-name { font-size: 11px; margin-top: 5px; }
  .wrap-label .product-title { top: 79px; font-size: 17px; line-height: 17px; }
  .wrap-label .net-weight { top: 124px; font-size: 12px; }

  .origin-block {
    position: absolute; left: 55px; top: 76px;
    font-size: 7px; font-weight: 600; line-height: 8.5px;
  }
  .origin-block .certifier { margin-top: 4px; }

  .info-block { position: absolute; left: 584px; top: 33px; width: 170px; }
  .info-heading { font-size: 8px; font-weight: 700; line-height: 10px; }
  .info-text { font-size: 5.2px; font-weight: 600; line-height: 6.6px; }
  .info-list { list-style: none; }
  .info-list li::before { content: "• "; }
  .info-block .info-heading + .info-text { margin-bottom: 4px; }

  .cert-row { display: flex; align-items: center; gap: 3px; margin-top: 8px; }
  .cert-badge-square { width: 24px; height: 16px; background: var(--badge-blue); }
  .cert-badge-round { width: 16px; height: 16px; border-radius: 50%; border: 1.5px solid var(--badge-green); background: var(--label-white); }
  .storage-note { font-size: 5.5px; font-weight: 700; line-height: 6.6px; text-transform: uppercase; margin-left: 9px; }
</style>
</head>
<body>
<main class="canvas">

  <section class="lid-label" aria-label="Lid label">
    <div class="brand-mark">
      <span class="brand-dot"></span>
      <span class="brand-name">Kesso Tea</span>
    </div>
    <svg class="title-frame" width="330" height="330" viewBox="0 0 330 330" aria-hidden="true">
      <polyline points="97,166 55,166 55,239 100,239" stroke-width="3"/>
      <polyline points="233,166 275,166 275,239 230,239" stroke-width="3"/>
    </svg>
    <h1 class="product-title">Premium<br>Organic<br>Ceremonial<br><span class="accent">Matcha</span></h1>
    <p class="net-weight">1oz</p>
  </section>

  <section class="wrap-label" aria-label="Jar wrap label">
    <div class="origin-block">
      <p>Product of Japan</p>
      <p>Distributed by:</p>
      <p>Kesso Tea Co. | Brookfield, Ga</p>
      <p class="certifier">Certified Organic by Verdan</p>
    </div>

    <div class="brand-mark">
      <span class="brand-dot"></span>
      <span class="brand-name">Kesso Tea</span>
    </div>
    <svg class="title-frame" width="770" height="150" viewBox="0 0 770 150" aria-hidden="true">
      <polyline points="290,85 263,85 263,108 280,108" stroke-width="2"/>
      <polyline points="482,85 507,85 507,108 490,108" stroke-width="2"/>
    </svg>
    <h2 class="product-title">Premium Organic<br>Ceremonial <span class="accent">Matcha</span></h2>
    <p class="net-weight">1oz</p>

    <div class="info-block">
      <p class="info-heading">Ingredients:</p>
      <p class="info-text">Premium Organic Japanese Matcha Green Tea</p>
      <p class="info-heading">Instructions:</p>
      <ul class="info-text info-list">
        <li>2 tsp of Matcha</li>
        <li>2oz of Water (170-180 degrees F)</li>
        <li>Whisk in a W formation until frothy</li>
        <li>Sweeten to taste</li>
      </ul>
      <div class="cert-row">
        <span class="cert-badge-square" role="img" aria-label="Non-GMO certification badge"></span>
        <span class="cert-badge-round" role="img" aria-label="Organic certification badge"></span>
        <p class="storage-note">Keep refrigerated<br>for quality</p>
      </div>
    </div>
  </section>

</main>
</body>
</html>
```